New Year's card HTML

can you produce a best new years wishes 2018 design in HTML for our website as what I would like to send by email towards my network of candidates / customers ...

It must be wow, inspiring , design, meaningfull... MMM those people care about me, or those people will help me to go the extra mile, to help me to achieve my career goals, Your best move, enhance my possibilities, bring the love back

Target Market(s)

CEo's / CMO's/ HRDirectors network of 450k

Coding

Coded - Design and coding required

Number of Pages Required

1 page

Colors

Designer to choose colors to be used in the design.

Requirements
Must have
• Logo / visual / website adress www.moravintel.com and a call to action
Should not have
• no sound as our business is confidential

```html
<!DOCTYPE html>
<html lang="en">
<head>
<meta charset="utf-8">
<title>Moravintel – Happy New Year 2018</title>
<link href="https://fonts.googleapis.com/css2?family=Cinzel:wght@400;500&family=Nunito:wght@600&display=swap" rel="stylesheet">
<style>
  :root {
    --night-deep: #140d08;
    --night-warm: #2e1d10;
    --wood-mid: #5a3e24;
    --wood-warm: #6f5134;
    --ink-white: #ffffff;
    --rule-white: rgba(255, 255, 255, 0.85);
    --accent-red: #b3101e;
    --accent-gold: #d6b100;
    --cta-orange: #ff8a00;
  }
  html, body {
    margin: 0;
    padding: 0;
    width: 929px;
    height: 1200px;
    overflow: hidden;
    background: var(--night-deep);
  }
  .greeting-card {
    position: relative;
    width: 929px;
    height: 1200px;
    overflow: hidden;
    font-family: "Cinzel", "Times New Roman", serif;
    color: var(--ink-white);
  }
  .backdrop-photo {
    position: absolute;
    inset: 0;
    background: linear-gradient(180deg,
      var(--night-deep) 0%,
      var(--night-warm) 45%,
      var(--night-deep) 68%,
      var(--wood-mid) 80%,
      var(--wood-warm) 100%);
  }
  .brand {
    position: absolute;
    left: 0; top: 58px;
    width: 929px;
    margin: 0;
    text-align: center;
    font-size: 58px;
    font-weight: 400;
    letter-spacing: 5px;
    line-height: 1;
  }
  .headline {
    position: absolute;
    left: 100px; top: 323px;
    width: 770px;
  }
  .headline .rule {
    height: 2px;
    background: var(--rule-white);
    margin-bottom: 4px;
  }
  .headline .rule.faint { height: 1px; opacity: 0.7; }
  .headline-text {
    margin: 12px 0 4px;
    text-align: center;
    font-size: 85px;
    font-weight: 400;
    line-height: 1.1;
    letter-spacing: 1px;
  }
  .year {
    position: absolute;
    left: 120px; top: 478px;
    width: 690px;
    text-align: center;
    font-size: 285px;
    font-weight: 500;
    line-height: 1;
    letter-spacing: 12px;
    text-shadow: -6px -5px 0 var(--accent-red), 7px 8px 0 var(--accent-gold);
  }
  .cta {
    position: absolute;
    left: 198px; top: 818px;
    width: 548px; height: 105px;
    border-radius: 40px;
    background: var(--cta-orange);
    color: var(--ink-white);
    font-family: "Nunito", "Helvetica Neue", Arial, sans-serif;
    font-weight: 600;
    font-size: 37px;
    letter-spacing: 1px;
    display: flex;
    align-items: center;
    justify-content: center;
    text-decoration: none;
  }
</style>
</head>
<body>
  <main class="greeting-card">
    <div class="backdrop-photo" role="img" aria-label="Photograph: blurred evening city lights above a wooden tabletop"></div>

    <header class="brand">MORAVINTEL</header>

    <section class="headline">
      <div class="rule"></div>
      <div class="rule faint"></div>
      <h1 class="headline-text">HAPPY NEW YEAR</h1>
      <div class="rule faint"></div>
      <div class="rule"></div>
    </section>

    <div class="year">2018</div>

    <a class="cta" href="http://www.moravintel.com">VISIT OUR WEBSITE</a>
  </main>
</body>
</html>
```